Business Landing Page for SEO Company

Need the landing page of the website designed - I will provide the copy, will need to include details of my company and the services offered, about us, testimonials, faq, etc., and all these elements will need to be arranged graphically on the page.

I want something similar to this: https://torvanequill.com/

Not in terms of color or theme or anything, but we offer a similar service and want to display similar information.

Th services we provide are:

Premium Links
Monthly Links Subscription
Link Insertions

Need to advertise them on the front page. Additionally need a place for testimonials, company details, etc.,

We already have logo for the website. Please use the attached file to insert the logo within the overal design.

Target Market(s)

SEO marketers and agencies

Number of Pages Required

1 page

```html
<!DOCTYPE html>
<html lang="en">
<head>
<meta charset="utf-8">
<title>Lumora — Link Building for SEO Agencies</title>
<link href="https://fonts.googleapis.com/css2?family=Montserrat:wght@400;500;600;700&display=swap" rel="stylesheet">
<style>
:root{
  --blue:#1b5fd9;
  --blue-deep:#0f3fb0;
  --blue-light:#3d86f0;
  --orange:#ff8a00;
  --ink:#1c2331;
  --muted:#6b7385;
  --grey-bg:#eef1f6;
  --line:#c9d8f2;
  --black:#0b0d12;
  --white:#ffffff;
}
*{box-sizing:border-box;margin:0;padding:0}
html,body{width:1200px;height:4819px;overflow:hidden}
body{font-family:'Montserrat',sans-serif;color:var(--ink);background:var(--white)}
.page{position:relative;width:1200px;height:4819px;overflow:hidden}
.abs{position:absolute}
a{color:inherit;text-decoration:none}

/* header */
.site-header{position:absolute;left:0;top:0;width:1200px;height:90px;background:var(--white);z-index:3}
.brand{position:absolute;left:127px;top:20px;font-size:46px;font-weight:600;color:var(--blue);letter-spacing:-1px}
.main-nav{position:absolute;left:407px;top:36px;display:flex;gap:56px;font-size:13px;font-weight:500;color:#6a7080}
.main-nav .active{color:var(--orange)}

/* hero */
.hero-bg{left:0;top:90px}
.hero-box{left:110px;top:256px;width:450px;height:263px;border:2px solid rgba(255,255,255,.75)}
.hero-title{left:152px;top:292px;color:#fff;font-weight:500;font-size:40px;line-height:1.1}
.hero-title strong{display:block;font-size:62px;font-weight:600}
.hero-sub{left:152px;top:430px;color:#fff;font-size:25px;font-weight:500}
.btn{display:inline-flex;align-items:center;justify-content:center;border-radius:30px;font-weight:600;letter-spacing:1px;font-size:14px}
.btn-solid{background:var(--orange);color:#fff}
.btn-line{border:2px solid var(--orange);color:var(--orange);background:#fff;border-radius:2px}
.hero-btn{left:152px;top:493px;width:196px;height:45px}
.hero-art{left:560px;top:112px;width:600px;height:580px;border-radius:24px;background:radial-gradient(circle at 55% 45%,#5fa8ff 0%,#2a6ee8 45%,rgba(27,95,217,0) 75%)}

/* about */
.about-frame{left:95px;top:797px;width:515px;height:515px}
.eyebrow{left:644px;top:904px;font-size:14px;font-weight:600;letter-spacing:2px;color:var(--blue)}
.about-title{left:644px;top:922px;font-size:34px;font-weight:600}
.title-rule{height:3px;background:var(--orange)}
.about-text{left:644px;top:1006px;width:440px;font-size:14.5px;line-height:29px;color:var(--muted)}
.about-btn{left:648px;top:1185px;width:168px;height:41px}

/* services */
.services{left:0;top:1357px;width:1200px;height:641px;background:linear-gradient(180deg,var(--blue) 0%,#1f63dd 60%,#2d72e8 100%)}
.services-wave{left:0;top:1720px;width:1200px;height:278px;background:radial-gradient(ellipse at 60% 100%,rgba(140,190,255,.55),rgba(30,100,225,0) 70%)}
.section-title{width:1200px;text-align:center;font-size:31px;font-weight:600}
.services .section-title{color:#fff}
.diamond{width:312px;height:312px;transform:rotate(45deg)}
.d-orange{background:var(--orange)}
.d-white{background:#fff;border:3px solid var(--blue);box-shadow:0 0 0 6px #fff inset}
.service{width:260px;text-align:center}
.service h3{font-size:18px;font-weight:600;margin:12px 0 12px}
.service p{font-size:12.5px;line-height:20px}
.service.on-orange{color:#fff}
.service.on-white h3{color:var(--ink)}
.service.on-white p{color:#3a4152}
.icon-ring{width:112px;height:112px;border-radius:50%;margin:0 auto;display:flex;align-items:center;justify-content:center}
.on-orange .icon-ring{border:3px solid #fff;background:#fff;box-shadow:0 0 0 4px var(--orange) inset}
.on-white .icon-ring{background:var(--blue);border:4px solid #dfe9fb}

/* testimonials */
.testimonial{width:305px;height:230px;border:2px solid #dbe6f7;background:#fff;text-align:center;padding:58px 30px 0}
.testimonial p{font-size:13px;line-height:21px;color:var(--muted)}
.testimonial h4{margin-top:16px;font-size:13px;font-weight:600}
.avatar{width:72px;height:72px;border-radius:50%;background:linear-gradient(135deg,#b9c2cf,#6e7786);border:3px solid #fff}
.dot{width:11px;height:11px;border-radius:50%;background:#8ab2ee}
.dot.on{background:var(--orange)}

/* blogs */
.blog-card{width:308px;height:374px;background:#fff;border:1px solid #dde3ec;text-align:center}
.blog-img{height:210px}
.blog-card h3{font-size:13.5px;font-weight:600;line-height:17px;margin:20px 28px 10px}
.blog-card p{font-size:10px;line-height:14px;color:var(--muted);margin:0 40px}
.blog-btn{margin-top:14px;width:112px;height:30px;font-size:9px;border-radius:16px;border-width:2px}

/* faq */
.faq-open{left:206px;top:3343px;width:771px;height:148px;background:var(--orange);color:#fff;padding:28px 34px}
.faq-open h4{font-size:12.5px;font-weight:600}
.faq-open p{font-size:11.5px;line-height:21px;margin-top:16px}
.faq-item{left:206px;width:771px;height:48px;border:2px solid #c9cfdb;padding:0 32px;display:flex;align-items:center;justify-content:space-between;font-size:11.5px;font-weight:500;color:#3a4a6a}
.chev{width:24px;height:24px}

/* contact */
.field{height:47px;border-radius:24px;background:#fff;padding:0 26px;display:flex;align-items:center;font-size:15px;color:#2b3244}
.field span{color:var(--orange)}
.message{left:189px;top:4163px;width:824px;height:124px;border-radius:14px;background:#fff;padding:22px 26px;font-size:15px;color:#2b3244}
.send-btn{left:492px;top:4311px;width:218px;height:47px;font-size:16px;letter-spacing:.5px}

/* footer */
.footer-brand{left:0;top:4440px;width:1200px;text-align:center;font-size:50px;font-weight:600;color:var(--blue);letter-spacing:-1px}
.f-head{font-size:16px;font-weight:600;color:#fff;letter-spacing:.5px}
.f-list{list-style:none;font-size:12px;color:#aab0bd}
.f-list li{height:33px}
.c-row{display:flex;gap:14px;align-items:flex-start}
.c-row b{display:block;font-size:11px;font-weight:600;color:#fff;margin-bottom:3px}
.c-row span{font-size:12px;color:#aab0bd}
.newsletter{left:848px;top:4592px;width:232px;height:34px;border-radius:17px;background:#1d2230;padding:0 4px 0 20px;display:flex;align-items:center;justify-content:space-between;font-size:11px;color:#9aa1af}
.socials{left:882px;top:4657px;display:flex;gap:9px}
.socials i{width:30px;height:30px;border-radius:50%;background:#fff;border:3px solid var(--orange);display:block}
.socials i:first-child{background:var(--orange);border-color:#fff}
.copyright{right:124px;top:4712px;text-align:right;font-size:11.5px;line-height:24px;color:#7c8392}
</style>
</head>
<body>
<div class="page">

  <header class="site-header">
    <div class="brand">Lumora</div>
    <nav class="main-nav">
      <a class="active">HOME</a><a>ABOUT US</a><a>SERVICES</a><a>TESTIMONIALS</a><a>FAQ</a><a>CONTACT</a>
    </nav>
  </header>

  <!-- hero -->
  <svg class="abs hero-bg" width="1200" height="720" viewBox="0 90 1200 720">
    <defs>
      <linearGradient id="heroGrad" x1="0" y1="0" x2="1" y2="1">
        <stop offset="0" stop-color="#1f6be6"/><stop offset="1" stop-color="#1346c4"/>
      </linearGradient>
    </defs>
    <polygon points="0,720 600,800 1200,720 1200,700 600,780 0,700" fill="#ff8a00"/>
    <polygon points="0,90 1200,90 1200,698 600,778 0,698" fill="url(#heroGrad)"/>
  </svg>
  <div class="abs hero-art" role="img" aria-label="Isometric illustration of people working at laptops around large analytics dashboards"></div>
  <div class="abs hero-box"></div>
  <h1 class="abs hero-title">Welcome to<strong>Lumora links</strong></h1>
  <p class="abs hero-sub">The Real done for you link</p>
  <a class="abs btn btn-solid hero-btn">LEARN MORE</a>

  <!-- about -->
  <svg class="abs about-frame" viewBox="0 0 515 515" role="img" aria-label="Photo of a hand touching a glowing SEO interface">
    <defs>
      <radialGradient id="aboutGrad" cx="0.5" cy="0.5" r="0.6">
        <stop offset="0" stop-color="#2a7fe0"/><stop offset="1" stop-color="#071a3d"/>
      </radialGradient>
    </defs>
    <polygon points="257,2 513,257 257,513 2,257" fill="none" stroke="#ff8a00" stroke-width="2"/>
    <polygon points="257,20 495,257 257,495 20,257" fill="url(#aboutGrad)"/>
  </svg>
  <div class="abs eyebrow">WHY WE ARE</div>
  <h2 class="abs about-title">ABOUT LUMORA</h2>
  <div class="abs title-rule" style="left:644px;top:974px;width:76px"></div>
  <p class="abs about-text">Lorem ipsum dolor sit amet, consectetur adipiscing elit, sed do eiusmod tempor incididunt ut labore et dolore magna aliqua. Ut enim ad minim veniam, quis nostrud exercitation ullamco laboris nisi Lorem ipsum dolor sit amet, consectetur adipiscing elit, sed do eiusmod</p>
  <a class="abs btn btn-line about-btn">LEARN MORE</a>

  <!-- services -->
  <section class="abs services"></section>
  <div class="abs services-wave" role="img" aria-label="Soft dotted wave pattern"></div>
  <h2 class="abs section-title" style="top:1405px">OUR SERVICES</h2>
  <div class="abs diamond d-orange" style="left:117px;top:1546px"></div>
  <div class="abs diamond d-orange" style="left:767px;top:1546px"></div>
  <div class="abs diamond d-white" style="left:443px;top:1546px"></div>

  <div class="abs service on-orange" style="left:139px;top:1560px">
    <div class="icon-ring">
      <svg width="48" height="48" viewBox="0 0 48 48" fill="none" stroke="#ff8a00" stroke-width="2.4"><rect x="4" y="8" width="40" height="30" rx="3"/><line x1="4" y1="15" x2="44" y2="15"/><rect x="10" y="20" width="14" height="8"/><path d="M28 26l10 5-4 1 3 5-2 1-3-5-3 3z" fill="#ff8a00"/></svg>
    </div>
    <h3>Premium Links</h3>
    <p>Lorem ipsum dolor sit amet, consectetur adipiscing elit, sed do eiusmod tempor incididunt u</p>
  </div>
  <div class="abs service on-white" style="left:469px;top:1558px">
    <div class="icon-ring">
      <svg width="50" height="50" viewBox="0 0 50 50" fill="none" stroke="#fff" stroke-width="2.4"><rect x="6" y="9" width="34" height="32" rx="3"/><line x1="6" y1="17" x2="40" y2="17"/><line x1="14" y1="5" x2="14" y2="12"/><line x1="32" y1="5" x2="32" y2="12"/><path d="M12 23h4M20 23h4M28 23h4M12 30h4M20 30h4"/><circle cx="38" cy="37" r="7" fill="#1b5fd9"/><path d="M35 37l2 2 4-4"/></svg>
    </div>
    <h3>Monthly Links<br>Subscription</h3>
    <p>Lorem ipsum dolor sit amet, consectetur adipiscing elit sed</p>
  </div>
  <div class="abs service on-orange" style="left:813px;top:1560px">
    <div class="icon-ring">
      <svg width="48" height="48" viewBox="0 0 48 48" fill="none" stroke="#ff8a00" stroke-width="3" stroke-linecap="round"><path d="M20 28l8-8"/><path d="M22 14l4-4a7 7 0 0 1 10 10l-4 4"/><path d="M26 34l-4 4a7 7 0 0 1-10-10l4-4"/></svg>
    </div>
    <h3>Link Insertions</h3>
    <p>Lorem ipsum dolor sit amet, consectetur adipiscing elit, sed do eiusmod tempor incididunt ut l</p>
  </div>

  <!-- testimonials -->
  <h2 class="abs section-title" style="top:2074px">TESTIMONIALS</h2>
  <div class="abs title-rule" style="left:563px;top:2122px;width:76px"></div>
  <div class="abs testimonial" style="left:122px;top:2215px"><p>Lorem ipsum dolor sit amet, consectetur adipiscing elit, sed do eiusmod tempor incididunt ut labore et dolore magna aliqua. Ut enim ad minim veniam, quis nostrud</p><h4>OWEN HARLOW</h4></div>
  <div class="abs testimonial" style="left:447px;top:2215px"><p>Lorem ipsum dolor sit amet, consectetur adipiscing elit, sed do eiusmod tempor incididunt ut labore et dolore magna aliqua. Ut enim ad minim veniam, quis nostrud</p><h4>RHYS TALBOT</h4></div>
  <div class="abs testimonial" style="left:769px;top:2215px"><p>Lorem ipsum dolor sit amet, consectetur adipiscing elit, sed do eiusmod tempor incididunt ut labore et dolore magna aliqua. Ut enim ad minim veniam, quis nostrud</p><h4>LENA MARSH</h4></div>
  <div class="abs avatar" style="left:238px;top:2180px" role="img" aria-label="Portrait of Owen Harlow"></div>
  <div class="abs avatar" style="left:563px;top:2180px" role="img" aria-label="Portrait of Rhys Talbot"></div>
  <div class="abs avatar" style="left:886px;top:2180px" role="img" aria-label="Portrait of Lena Marsh"></div>
  <div class="abs dot" style="left:572px;top:2485px"></div>
  <div class="abs dot" style="left:594px;top:2485px"></div>
  <div class="abs dot on" style="left:616px;top:2485px"></div>

  <!-- blogs -->
  <svg class="abs" style="left:0;top:2552px" width="1200" height="615" viewBox="0 0 1200 615"><polygon points="0,0 1200,0 1200,613 400,585 0,565" fill="#eef1f6"/></svg>
  <h2 class="abs section-title" style="top:2608px">LATEST BLOGS</h2>
  <article class="abs blog-card" style="left:125px;top:2707px">
    <div class="blog-img" role="img" aria-label="Circuit board with glowing SEO chip" style="background:linear-gradient(135deg,#0a2a55,#1d6fd0 60%,#0c2a4f)"></div>
    <h3>Lorem ipsum dolor sit amet, consectetur adipiscing elit, sed do</h3>
    <p>Lorem ipsum dolor sit amet, consectetur adipiscing elit, sed do eiusmod tempor</p>
    <a class="btn btn-line blog-btn">LEARN MORE</a>
  </article>
  <article class="abs blog-card" style="left:451px;top:2707px">
    <div class="blog-img" role="img" aria-label="Hand holding a pen below an SEO search bar" style="background:linear-gradient(135deg,#6b6f76,#c9b6a3 55%,#8a7c70)"></div>
    <h3>Lorem ipsum dolor sit amet, consectetur adipiscing elit, sed do</h3>
    <p>Lorem ipsum dolor sit amet, consectetur adipiscing elit, sed do eiusmod tempor</p>
    <a class="btn btn-line blog-btn">LEARN MORE</a>
  </article>
  <article class="abs blog-card" style="left:775px;top:2707px">
    <div class="blog-img" role="img" aria-label="Hands on a laptop with floating SEO icons" style="background:linear-gradient(135deg,#7fa6d8,#3c6fb8 55%,#d58a7a)"></div>
    <h3>Lorem ipsum dolor sit amet, consectetur adipiscing elit, sed do</h3>
    <p>Lorem ipsum dolor sit amet, consectetur adipiscing elit, sed do eiusmod tempor</p>
    <a class="btn btn-line blog-btn">LEARN MORE</a>
  </article>

  <!-- faq -->
  <h2 class="abs section-title" style="top:3251px;font-size:26px">FREQUENTLY ASKED QUESTIONS</h2>
  <div class="abs title-rule" style="left:563px;top:3294px;width:76px"></div>
  <div class="abs faq-open">
    <h4>Lorem ipsum dolor sit amet, consectetur adipiscing elit ?</h4>
    <p>Sed ut perspiciatis unde omnis iste natus error sit voluptatem accusantium doloremque laudantium, totam rem aperiam, eaque ipsa quae ab illo inventore veritatis et quasi architecto beatae vitae dicta sunt explicabo. Nemo enim ipsam voluptatem quia voluptas sit aspernatur aut odit aut fugit, sed quia consequuntur magni dolores eos</p>
    <svg class="abs chev" style="right:18px;top:14px" viewBox="0 0 24 24" fill="none" stroke="#fff" stroke-width="1.5"><circle cx="12" cy="12" r="10.5"/><path d="M7.5 14l4.5-4 4.5 4"/></svg>
  </div>
  <div class="abs faq-item" style="top:3510px">Sed ut perspiciatis unde omnis iste natus ?<svg class="chev" viewBox="0 0 24 24" fill="none" stroke="#1b5fd9" stroke-width="1.5"><circle cx="12" cy="12" r="10.5"/><path d="M7.5 10l4.5 4 4.5-4"/></svg></div>
  <div class="abs faq-item" style="top:3569px">Error sit voluptatem accusantium doloremque laudantium ?<svg class="chev" viewBox="0 0 24 24" fill="none" stroke="#1b5fd9" stroke-width="1.5"><circle cx="12" cy="12" r="10.5"/><path d="M7.5 10l4.5 4 4.5-4"/></svg></div>
  <div class="abs faq-item" style="top:3628px">Ttotam rem aperiam, eaque ipsa quae ab illo inventore ?<svg class="chev" viewBox="0 0 24 24" fill="none" stroke="#1b5fd9" stroke-width="1.5"><circle cx="12" cy="12" r="10.5"/><path d="M7.5 10l4.5 4 4.5-4"/></svg></div>
  <div class="abs faq-item" style="top:3688px">Weritatis et quasi architecto beatae vitae dicta ?<svg class="chev" viewBox="0 0 24 24" fill="none" stroke="#1b5fd9" stroke-width="1.5"><circle cx="12" cy="12" r="10.5"/><path d="M7.5 10l4.5 4 4.5-4"/></svg></div>

  <!-- contact + footer backgrounds -->
  <svg class="abs" style="left:0;top:3772px" width="1200" height="1047" viewBox="0 3772 1200 1047">
    <defs>
      <linearGradient id="contactGrad" x1="0" y1="0" x2="0" y2="1">
        <stop offset="0" stop-color="#1b5fd9"/><stop offset="1" stop-color="#2a6fe6"/>
      </linearGradient>
      <radialGradient id="contactGlow" cx="0.5" cy="1" r="0.7">
        <stop offset="0" stop-color="#8ec0ff" stop-opacity=".55"/><stop offset="1" stop-color="#2a6fe6" stop-opacity="0"/>
      </radialGradient>
    </defs>
    <polygon points="0,3772 600,3899 1200,3772 1200,4819 0,4819" fill="url(#contactGrad)"/>
    <rect x="0" y="4200" width="1200" height="300" fill="url(#contactGlow)"/>
    <path d="M0,4465 Q600,4505 1200,4465 L1200,4819 L0,4819 Z" fill="#0b0d12"/>
  </svg>

  <h2 class="abs section-title" style="top:3945px;color:#fff;font-size:26px">FILL OUR CONTACT FORM</h2>
  <div class="abs title-rule" style="left:569px;top:3988px;width:62px;background:#fff"></div>
  <div class="abs field" style="left:183px;top:4025px;width:407px">First Name<span>*</span></div>
  <div class="abs field" style="left:601px;top:4025px;width:408px">Last Name<span>*</span></div>
  <div class="abs field" style="left:183px;top:4094px;width:407px">Contact Number<span>*</span></div>
  <div class="abs field" style="left:601px;top:4094px;width:408px">E-mail<span>*</span></div>
  <div class="abs message">Leave a Message</div>
  <a class="abs btn btn-solid send-btn">SEND MESSAGE</a>

  <!-- footer -->
  <div class="abs footer-brand">Lumora</div>
  <div class="abs f-head" style="left:140px;top:4554px">INFORMATION</div>
  <ul class="abs f-list" style="left:141px;top:4592px"><li>Home</li><li>About Us</li><li>Services</li><li>News &amp; Blogs</li><li>Contact</li></ul>
  <div class="abs f-head" style="left:355px;top:4554px">LINKS</div>
  <ul class="abs f-list" style="left:357px;top:4592px"><li>Careers</li><li>Support</li><li>Sitemap</li><li>Privacy Policy</li><li>Contact Us</li></ul>
  <div class="abs f-head" style="left:545px;top:4554px">CONTACT US</div>
  <div class="abs c-row" style="left:548px;top:4590px">
    <svg width="28" height="30" viewBox="0 0 28 30" fill="none" stroke="#fff" stroke-width="1.6"><path d="M14 26s-8-8-8-14a8 8 0 0 1 16 0c0 6-8 14-8 14z"/><circle cx="14" cy="12" r="3"/><ellipse cx="14" cy="27" rx="11" ry="2.5"/></svg>
    <div><b>ADDRESS</b><span>418 Alder Crest Lane Fairhollow</span></div>
  </div>
  <div class="abs c-row" style="left:548px;top:4646px">
    <svg width="28" height="28" viewBox="0 0 28 28" fill="none" stroke="#fff" stroke-width="1.6"><path d="M6 3l5 5-3 3c1 3 5 7 8 8l3-3 5 5-3 3C12 25 3 16 3 6z"/></svg>
    <div><b>PHONE</b><span style="font-size:13px">(555)-014-2290</span></div>
  </div>
  <div class="abs c-row" style="left:548px;top:4702px">
    <svg width="28" height="24" viewBox="0 0 28 24" fill="none" stroke="#fff" stroke-width="1.6"><rect x="2" y="4" width="24" height="16"/><path d="M2 4l12 9 12-9"/></svg>
    <div><b>EMAIL US</b><span style="font-size:13px">enquiry@lumora.co</span></div>
  </div>
  <div class="abs f-head" style="left:848px;top:4560px">NEWSLETTER</div>
  <div class="abs newsletter">Your E-mail
    <svg width="26" height="26" viewBox="0 0 26 26"><circle cx="13" cy="13" r="13" fill="#1b5fd9"/><path d="M7 13h11M14 9l4 4-4 4" stroke="#fff" stroke-width="2" fill="none"/></svg>
  </div>
  <div class="abs socials" aria-label="Social profiles"><i></i><i></i><i></i><i></i><i></i></div>
  <div class="abs copyright">Copyright © 2021 Lumora<br>All Right Reserved</div>

</div>
</body>
</html>
```